real esate business card with company logo and name

we need a business card design for a real esate company

The company name is Walsh & Brand Pty Ltd, and we have our logo designed and will upload. We want classic or moden feel. Black or white background. looks more textured. Should include folowinginformations
Owen Walsh and Lucy Brand
Sales Agents & Onsite Manager
p: 07 5948 2063
F: 07 5948 2174
M:0431 857 219
3/42 Marlow Crescent, FERNLEA QLD 4213

We want this business card looks professonal. Thank you in advance.

Industry/Entity Type

Real Estate Agent

Contact Information for Business Card

Owen Walsh and Lucy Brand
Onsite Manager & Sales Agents
p: 07 5948 2063
M:0431 857 219

Font styles to use
Serif

Colors
000000
fbfbfb
333333
959595

Requirements
Must have
• company logo and name, black or white back ground

```html
<!DOCTYPE html>
<html lang="en">
<head>
<meta charset="utf-8">
<title>Walsh &amp; Brand Pty Ltd — Business Card</title>
<link rel="stylesheet" href="https://fonts.googleapis.com/css2?family=Lato:wght@400;700&family=Oswald:wght@400&display=swap">
<style>
  :root {
    --backdrop: #e9e9e9;
    --card: #fbfbfb;
    --ink: #333333;
    --ink-soft: #4a4a4a;
    --grey: #959595;
    --band-light: #a9a9a9;
    --band-dark: #4b4b4b;
    --mark-light: #cfcfcf;
    --black: #000000;
  }
  html, body {
    margin: 0;
    width: 1200px;
    height: 900px;
    overflow: hidden;
    background: var(--backdrop);
  }
  .stage { position: relative; width: 1200px; height: 900px; }
  .card {
    position: absolute;
    background: var(--card);
    box-shadow: 0 6px 18px rgba(0,0,0,.18);
    overflow: hidden;
  }
  .card-front { left: 238px; top: 62px; width: 555px; height: 343px; }
  .card-back  { left: 457px; top: 518px; width: 560px; height: 344px; }

  .front-names {
    position: absolute; left: 41px; top: 35px; margin: 0;
    font: 700 20px/1 "Lato", sans-serif; color: var(--ink);
  }
  .front-role {
    position: absolute; left: 41px; top: 63px; margin: 0;
    font: 400 15px/1 "Lato", sans-serif; color: var(--ink-soft);
  }
  .front-address {
    position: absolute; left: 41px; top: 121px; margin: 0;
    font: 400 14px/17px "Lato", sans-serif; color: var(--ink);
    font-style: normal;
  }
  .front-contacts {
    position: absolute; left: 41px; top: 174px; margin: 0; padding: 0;
    list-style: none; font: 400 14px/21px "Lato", sans-serif; color: var(--ink);
  }
  .front-contacts li { display: flex; align-items: center; gap: 9px; }
  .front-contacts svg { width: 12px; height: 12px; fill: var(--ink); }

  .front-brand {
    position: absolute; left: 320px; top: 40px; width: 200px;
    display: flex; flex-direction: column; align-items: center;
  }
  .brand-square { width: 110px; height: 110px; background: var(--grey); }
  .front-brand .brand-name {
    margin-top: 42px;
    font: 400 12.5px/1 "Lato", sans-serif; letter-spacing: 1px; color: var(--ink-soft);
    white-space: nowrap;
  }

  .front-band {
    position: absolute; left: 0; right: 0; bottom: 0; height: 95px;
    background: linear-gradient(to right, var(--band-light) 0 382px, var(--band-dark) 382px 100%);
  }
  .band-badge {
    position: absolute; left: 400px; top: 14px; width: 96px; height: 70px;
    background: var(--black);
  }

  .back-brand {
    position: absolute; left: 0; right: 0; top: 55px;
    display: flex; flex-direction: column; align-items: center;
  }
  .back-brand .brand-square { width: 160px; height: 160px; background: var(--grey); }
  .back-brand .brand-name {
    margin-top: 30px;
    font: 400 29px/1 "Oswald", sans-serif; letter-spacing: 1px; color: var(--grey);
    white-space: nowrap;
  }
</style>
</head>
<body>
<main class="stage">
  <section class="card card-front" aria-label="Business card front">
    <h1 class="front-names">Owen Walsh and Lucy Brand</h1>
    <p class="front-role">Onsite Manager &amp; Sales Agents</p>
    <address class="front-address">3/42 Marlow Crescent, FERNLEA<br>QLD 4213</address>
    <ul class="front-contacts">
      <li>
        <svg viewBox="0 0 12 12" aria-hidden="true"><path d="M3.5 0h5a1 1 0 0 1 1 1v10a1 1 0 0 1-1 1h-5a1 1 0 0 1-1-1V1a1 1 0 0 1 1-1zm.3 1.5v8h4.4v-8zM6 10.2a.6.6 0 1 0 0 1.2.6.6 0 0 0 0-1.2z"/></svg>
        07 5948 2063
      </li>
      <li>
        <svg viewBox="0 0 12 12" aria-hidden="true"><path d="M1 3.5C1 2 3 1 6 1s5 1 5 2.5v1H8.5v-1h-5v1H1zM3 6l1.5-1.5h3L9 6l1.5 5h-9zm3 .8a1.5 1.5 0 1 0 0 3 1.5 1.5 0 0 0 0-3z"/></svg>
        0431 857 219
      </li>
    </ul>
    <div class="front-brand">
      <div class="brand-square" aria-hidden="true"></div>
      <span class="brand-name">WALSH &amp; BRAND PTY LTD.</span>
    </div>
    <div class="front-band">
      <div class="band-badge" aria-hidden="true"></div>
    </div>
  </section>

  <section class="card card-back" aria-label="Business card back">
    <div class="back-brand">
      <div class="brand-square" aria-hidden="true"></div>
      <span class="brand-name">WALSH &amp; BRAND PTY LTD.</span>
    </div>
  </section>
</main>
</body>
</html>
```